Coastline Premier Retreats Business Card Design

Design a business card for Coastline Premier Retreats. Look at the website for colors and reference. Card should have logo, name, title, office number, mobile number, email, URL and a tagline like, "Luxury Hotel & Resort Email Marketing" (This might change).

https://www.coastlinepremierretreats.example

The rest I will leave up to your imagination.

Contact Information for Business Card

Logo, name, title, office number, mobile number, email, URL and a tagline like, "Luxury Hotel & Resort Email Marketing" (This might change).

```html
<!DOCTYPE html>
<html lang="en">
<head>
<meta charset="utf-8">
<title>Coastline Premier Retreats – Business Card</title>
<link href="https://fonts.googleapis.com/css2?family=Montserrat:ital,wght@0,400;0,500;0,700;0,800;1,400&display=swap" rel="stylesheet">
<style>
  :root {
    --page: #2a2a2a;
    --card: #1b1b1b;
    --orange: #f07214;
    --white: #ffffff;
    --muted-mark: #4a4a4a;
  }
  * { box-sizing: border-box; margin: 0; padding: 0; }
  html, body {
    width: 1200px; height: 900px; overflow: hidden;
    background: var(--page);
    font-family: "Montserrat", Arial, sans-serif;
  }
  .sheet {
    width: 1200px; height: 900px;
    display: flex; flex-direction: column; align-items: center; justify-content: center;
    gap: 40px;
  }
  .card {
    position: relative;
    width: 700px; height: 400px;
    background: var(--card);
    box-shadow: 0 12px 30px rgba(0,0,0,.45);
    overflow: hidden;
  }

  /* Front */
  .name-flag {
    position: absolute; left: 40px; top: 62px;
    width: 14px; height: 36px; background: var(--orange);
  }
  .person-name {
    position: absolute; left: 68px; top: 60px;
    font-size: 34px; font-weight: 800; letter-spacing: .5px;
    color: var(--orange); text-transform: uppercase; line-height: 1;
  }
  .person-title {
    position: absolute; left: 70px; top: 102px;
    font-size: 15px; color: var(--white); font-weight: 400;
  }
  .title-rule {
    position: absolute; left: 190px; top: 113px;
    width: 460px; height: 1px; background: var(--orange);
  }
  .contact-list {
    position: absolute; left: 46px; top: 140px;
    list-style: none;
    font-size: 14.5px; color: var(--white);
  }
  .contact-list li {
    display: flex; align-items: center; gap: 10px;
    height: 24px;
  }
  .contact-list svg { width: 13px; height: 13px; flex: none; }
  .brand-name {
    position: absolute; right: 50px; top: 150px;
    font-size: 21px; font-weight: 700; color: var(--white);
    text-transform: uppercase; letter-spacing: 1px;
    display: flex; align-items: center; gap: 10px;
  }
  .brand-name .brand-square {
    width: 14px; height: 14px; background: var(--orange); flex: none;
  }
  .address {
    position: absolute; right: 50px; top: 292px;
    text-align: right;
    font-size: 15px; line-height: 1.45; color: var(--white);
  }
  .base-band {
    position: absolute; left: 0; right: 0; bottom: 0;
    height: 20px; background: var(--orange);
  }

  /* Back */
  .back-brand {
    position: absolute; right: 60px; top: 70px;
    text-align: right;
    font-size: 46px; font-weight: 800; line-height: 1.05;
    color: var(--muted-mark); text-transform: uppercase;
  }
  .tagline {
    position: absolute; left: 60px; bottom: 64px;
    font-size: 22px; font-style: italic; font-weight: 400;
    color: var(--orange);
  }
</style>
</head>
<body>
<main class="sheet">

  <section class="card card-front" aria-label="Business card front">
    <div class="name-flag"></div>
    <h1 class="person-name">Daniel Whitford</h1>
    <p class="person-title">CEO/Founder</p>
    <div class="title-rule"></div>

    <ul class="contact-list">
      <li>
        <svg viewBox="0 0 12 12" aria-hidden="true"><rect x="3" y="0.5" width="6" height="11" rx="1" fill="none" stroke="var(--orange)" stroke-width="1.2"/><circle cx="6" cy="9.5" r=".7" fill="var(--orange)"/></svg>
        555.204.7100
      </li>
      <li>
        <svg viewBox="0 0 12 12" aria-hidden="true"><path d="M1 4.5 Q6 1 11 4.5 L10 6 L8 5 L8 4 Q6 3.4 4 4 L4 5 L2 6 Z" fill="var(--orange)"/><rect x="2.5" y="6.5" width="7" height="4.5" rx=".8" fill="var(--orange)"/></svg>
        +34 600 000 214
      </li>
      <li>
        <svg viewBox="0 0 12 12" aria-hidden="true"><rect x="0.5" y="2.5" width="11" height="7" fill="var(--orange)"/><path d="M0.5 2.5 L6 7 L11.5 2.5" fill="none" stroke="var(--card)" stroke-width="1"/></svg>
        info@coastlinepremierretreats.example
      </li>
      <li>
        <svg viewBox="0 0 12 12" aria-hidden="true"><circle cx="6" cy="6" r="5.3" fill="var(--orange)"/><ellipse cx="6" cy="6" rx="2.3" ry="5.3" fill="none" stroke="var(--card)" stroke-width=".8"/><line x1=".7" y1="6" x2="11.3" y2="6" stroke="var(--card)" stroke-width=".8"/></svg>
        www.coastlinepremierretreats.example
      </li>
    </ul>

    <div class="brand-name"><span class="brand-square"></span>Coastline Premier Retreats</div>

    <address class="address" style="font-style:normal">
      PO Box 48, 210 Harbor Lane<br>
      Seaview, ME 04011
    </address>

    <div class="base-band"></div>
  </section>

  <section class="card card-back" aria-label="Business card back">
    <div class="back-brand">Coastline<br>Premier<br>Retreats</div>
    <p class="tagline">Luxury Hotel &amp; Resort Email Marketing</p>
  </section>

</main>
</body>
</html>
```